Business Card Design Project

Actor, Producer, Vocal Coach, Choral Director, Song WriterPhone: (215) 555-0142 Fax: (215) 856-3933Email: waltierblocker@gmail.comFacebook: facebook.com/waltier.blockerTwitter: @thedf482

Industry/Entity Type

Business

Contact Information for Business Card

Business Cards that include my picture

Colors

Designer to choose colors to be used in the design.

```html
<!DOCTYPE html>
<html lang="en">
<head>
<meta charset="utf-8">
<title>Dorian Fellsmore – Business Card</title>
<link rel="stylesheet" href="https://fonts.googleapis.com/css2?family=Arvo:wght@700&family=Great+Vibes&family=Open+Sans:wght@700&family=Playfair+Display:wght@400&display=swap">
<style>
  :root {
    --page: #ffffff;
    --maroon: #561414;
    --maroon-mid: #7a3a1e;
    --glow: #c98b5b;
    --script-blue: #27a6df;
    --white: #ffffff;
    --suit: #6f7c8c;
  }
  * { margin: 0; padding: 0; box-sizing: border-box; }
  html, body {
    width: 1200px; height: 1200px; overflow: hidden;
    background: var(--page);
  }
  .card {
    position: absolute;
    background: var(--maroon);
    box-shadow: 6px 6px 6px rgba(0,0,0,0.45);
    overflow: hidden;
    color: var(--white);
  }
  .card-front {
    left: 185px; top: 86px; width: 828px; height: 466px;
    background: radial-gradient(ellipse 340px 240px at 391px 218px, var(--glow) 0%, var(--maroon-mid) 50%, var(--maroon) 100%);
  }
  .card-back {
    left: 185px; top: 600px; width: 830px; height: 482px;
    background: radial-gradient(ellipse 380px 260px at 415px 230px, var(--glow) 0%, var(--maroon-mid) 50%, var(--maroon) 100%);
  }
  .name-script {
    font-family: "Great Vibes", cursive;
    color: var(--script-blue);
    line-height: 1;
    position: absolute;
  }
  .name-slab {
    font-family: "Arvo", serif;
    font-weight: 700;
    color: var(--white);
    line-height: 1;
    position: absolute;
  }
  .roles {
    font-family: "Playfair Display", serif;
    color: var(--white);
    position: absolute;
    letter-spacing: 0.5px;
  }
  /* front */
  .card-front .name-script { left: 66px; top: 12px; font-size: 78px; }
  .card-front .name-slab { left: 79px; top: 86px; font-size: 48px; }
  .card-front .roles { left: 354px; top: 62px; font-size: 27px; line-height: 40px; }
  .portrait {
    position: absolute; left: 23px; top: 162px; width: 376px; height: 304px;
    background: radial-gradient(ellipse 120px 120px at 160px 80px, #5b3526 0%, transparent 90%),
                linear-gradient(180deg, transparent 45%, var(--suit) 75%);
    border-radius: 46% 46% 0 0 / 40% 40% 0 0;
  }
  .contact-list { position: absolute; left: 410px; top: 225px; list-style: none; }
  .contact-item {
    display: flex; align-items: center;
    height: 46px;
    font-family: "Open Sans", sans-serif; font-weight: 700; font-size: 19px;
  }
  .contact-icon { width: 38px; height: 38px; margin-right: 29px; flex: none; }
  .contact-icon * { fill: none; stroke: var(--white); stroke-width: 2; }
  /* back */
  .card-back .name-script { left: 0; width: 100%; text-align: center; top: 40px; font-size: 150px; text-shadow: 0 6px 14px rgba(0,0,0,0.35); }
  .card-back .name-slab { left: 0; width: 100%; text-align: center; top: 186px; font-size: 92px; text-shadow: 0 8px 14px rgba(0,0,0,0.35); }
  .card-back .roles { left: 215px; top: 322px; font-size: 29px; line-height: 40px; }
</style>
</head>
<body>

<section class="card card-front">
  <div class="name-script">Dorian</div>
  <div class="name-slab">Fellsmore</div>
  <p class="roles">Actor, Producer, Vocal Coach,<br>Choral Director, Song Writer</p>
  <div class="portrait" role="img" aria-label="Portrait photo of Dorian Fellsmore in a grey suit and pink tie"></div>
  <ul class="contact-list">
    <li class="contact-item">
      <svg class="contact-icon" viewBox="0 0 38 38"><circle cx="19" cy="19" r="17"/><path d="M12 11c2-2 4 2 5 4s-2 2-1 4 3 4 5 5 2-3 4-1 4 3 2 5-6 1-10-3-7-12-5-14z"/></svg>
      (215) 555-0142
    </li>
    <li class="contact-item">
      <svg class="contact-icon" viewBox="0 0 38 38"><rect x="4" y="14" width="30" height="20" rx="2"/><rect x="11" y="4" width="16" height="14"/><rect x="4" y="14" width="6" height="20"/><path d="M14 8h10M14 11h10M15 22h14M15 26h14M15 30h14"/></svg>
      (215) 555-0187
    </li>
    <li class="contact-item">
      <svg class="contact-icon" viewBox="0 0 38 38"><circle cx="19" cy="19" r="17"/><rect x="10" y="13" width="18" height="12"/><path d="M10 13l9 7 9-7"/></svg>
      dorianfellsmore@postlane.net
    </li>
    <li class="contact-item">
      <svg class="contact-icon" viewBox="0 0 38 38"><circle cx="19" cy="19" r="15"/></svg>
      socialpage.net/dorian.fellsmore
    </li>
    <li class="contact-item">
      <svg class="contact-icon" viewBox="0 0 38 38"><circle cx="19" cy="19" r="15"/></svg>
      @thedf482
    </li>
  </ul>
</section>

<section class="card card-back">
  <div class="name-script">Dorian</div>
  <div class="name-slab">Fellsmore</div>
  <p class="roles">Actor, Producer, Vocal Coach,<br>Choral Director, Song Writer</p>
</section>

</body>
</html>
```